Solution Matrix for our Company

Develop an image that describes our "4 solutions". We eventually will list the products and services we have that address the solution being discussed. Our main website is http://brightlanework.com/. Feel free to look through the material there as well as the material we are addressing.

The mock document is a summary of the 4 solution buckets. We have also attached some samples from states that have done similar work. Feel free to be creative and use graphics and/or pictures in your design

Target Market(s)

Education

```html
<!DOCTYPE html>
<html lang="en">
<head>
<meta charset="utf-8">
<title>BLW Career Readiness Model</title>
<link href="https://fonts.googleapis.com/css2?family=Bebas+Neue&family=Oswald:wght@400;500&family=Roboto+Condensed:wght@400;700&family=Roboto:wght@700&display=swap" rel="stylesheet">
<style>
  :root{
    --orange:#f28c1c;
    --charcoal:#2b2e35;
    --ring:#55575c;
    --ink:#1f1f1f;
    --white:#ffffff;
  }
  *{margin:0;padding:0;box-sizing:border-box}
  html,body{width:1200px;height:900px;overflow:hidden;background:var(--white)}
  .sheet{position:relative;width:1200px;height:900px;overflow:hidden;font-family:"Roboto Condensed",sans-serif;color:var(--ink)}
  .backdrop{position:absolute;inset:0}

  .brand{position:absolute;left:0;top:0;width:293px;height:145px;display:flex;align-items:center;justify-content:center;gap:10px}
  .brand-dot{width:26px;height:26px;border-radius:50%;background:var(--orange)}
  .brand-name{font-family:"Oswald",sans-serif;font-weight:500;font-size:25px;color:var(--orange);letter-spacing:.5px}
  .title{position:absolute;left:330px;top:16px;font-family:"Bebas Neue",sans-serif;font-weight:400;font-size:92px;line-height:1;color:var(--white);white-space:nowrap;letter-spacing:-.5px}
  .mission{position:absolute;left:334px;top:110px;font-family:"Roboto",sans-serif;font-weight:700;font-size:20px;letter-spacing:7.6px;color:var(--white);white-space:nowrap}

  .block{position:absolute}
  .block h2{font-family:"Bebas Neue",sans-serif;font-weight:400;font-size:50px;line-height:.84;color:var(--orange)}
  .block p{font-size:17.5px;line-height:23.5px}
  .block ul{list-style:none;margin-top:20px}
  .block li{font-weight:700;font-size:17.5px;line-height:23.6px}
  .block.left li::before{content:"• "}
  .block.right{text-align:right}
  .block.right li::after{content:"  •"}
  .block.right li.cont{margin-right:10px}
  .block.right li.cont::after{content:""}
  .on-dark{color:var(--white)}

  .icon{position:absolute;width:100px;height:100px;border-radius:50%;border:6px solid var(--white);box-shadow:0 4px 10px rgba(0,0,0,.25)}
  .icon.dark{background:var(--ring)}
  .icon.orange{background:var(--orange)}

  .hub{position:absolute;left:420px;top:340px;width:360px;text-align:center}
  .hub h3{font-family:"Oswald",sans-serif;font-weight:400;font-size:30px;line-height:34px;color:var(--orange)}
  .hub p{font-size:15px;line-height:20.5px;margin-top:10px}
  .hub h4{font-family:"Oswald",sans-serif;font-weight:400;font-size:29px;color:var(--orange);margin-top:14px;line-height:34px}
  .hub ul{list-style:none;text-align:left;margin:6px 0 0 80px}
  .hub li{font-size:15px;line-height:20.5px}
  .hub li::before{content:"•";display:inline-block;width:16px}
</style>
</head>
<body>
<main class="sheet">
  <svg class="backdrop" width="1200" height="900" viewBox="0 0 1200 900" aria-hidden="true">
    <defs>
      <linearGradient id="headerFill" x1="0" y1="0" x2="0" y2="1">
        <stop offset="0" stop-color="#f7981f"/><stop offset="1" stop-color="#e8800f"/>
      </linearGradient>
      <linearGradient id="lightFill" x1="0" y1="0" x2="1" y2="1">
        <stop offset="0" stop-color="#ffffff"/><stop offset="1" stop-color="#e6e6e6"/>
      </linearGradient>
      <radialGradient id="hubFill" cx=".5" cy=".45" r=".55">
        <stop offset="0" stop-color="#ffffff"/><stop offset=".7" stop-color="#efefef"/><stop offset="1" stop-color="#d2d2d2"/>
      </radialGradient>
      <linearGradient id="brandFill" x1="0" y1="0" x2="1" y2="1">
        <stop offset="0" stop-color="#f4f4f4"/><stop offset="1" stop-color="#dcdcdc"/>
      </linearGradient>
    </defs>
    <rect x="0" y="0" width="1200" height="154" fill="url(#headerFill)"/>
    <path d="M0 0H293V115Q293 145 263 145H0Z" fill="url(#brandFill)"/>
    <rect x="0" y="150" width="1200" height="4" fill="#ffffff"/>
    <rect x="0" y="154" width="1200" height="734" fill="url(#lightFill)"/>
    <polygon points="656,154 1200,154 1200,499 574,499" fill="#5a5c62"/>
    <polygon points="670,154 1200,154 1200,499 588,499" fill="var(--charcoal)"/>
    <polygon points="0,499 624,499 702,888 0,888" fill="#5a5c62"/>
    <polygon points="0,499 610,499 688,888 0,888" fill="var(--charcoal)"/>
    <circle cx="600" cy="491" r="241" fill="var(--ring)"/>
    <circle cx="600" cy="491" r="222" fill="none" stroke="#ffffff" stroke-width="5" stroke-dasharray="9 6"/>
    <circle cx="600" cy="491" r="209" fill="#ffffff"/>
    <circle cx="600" cy="491" r="200" fill="url(#hubFill)"/>
    <rect x="0" y="888" width="1200" height="12" fill="var(--orange)"/>
  </svg>

  <div class="brand">
    <span class="brand-dot"></span><span class="brand-name">BRIGHTLANE WORK</span>
  </div>
  <h1 class="title">BLW CAREER READINESS MODEL</h1>
  <div class="mission">OUR MISSION IS TO ENSURE ALL STUDENTS ARE:</div>

  <div class="icon dark" style="left:46px;top:162px" role="img" aria-label="Icon of a person climbing onto a block"></div>
  <section class="block left" style="left:47px;top:180px;width:560px">
    <h2 style="position:absolute;left:136px;top:0">CAREER<br>SUPPORTED</h2>
    <p style="margin-top:98px">Students benefit from informed educational leadership<br>and policy making that result in effective career<br>resources and learning opportunities.</p>
    <ul>
      <li>BLW Policy Tools</li>
      <li>Workforce Act Technical Support</li>
      <li>Professional Development</li>
      <li>Industry-Education Relationships</li>
    </ul>
  </section>

  <div class="icon orange" style="left:1053px;top:162px" role="img" aria-label="Magnifying glass over a briefcase">
    <svg width="88" height="88" viewBox="0 0 88 88" aria-hidden="true">
      <circle cx="38" cy="38" r="19" fill="none" stroke="#fff" stroke-width="6"/>
      <line x1="52" y1="52" x2="66" y2="66" stroke="#fff" stroke-width="8" stroke-linecap="round"/>
      <rect x="29" y="33" width="18" height="12" rx="2" fill="#fff"/>
      <rect x="34" y="29" width="8" height="5" rx="1" fill="none" stroke="#fff" stroke-width="2"/>
    </svg>
  </div>
  <section class="block right on-dark" style="right:48px;top:178px;width:520px">
    <h2 style="margin-right:121px">CAREER<br>PREPARED</h2>
    <p style="margin-top:16px">Students have the necessary foundational,<br>technical, and workplace skills needed to<br>support success in a variety of careers.</p>
    <ul>
      <li>Career-Focused Curricula</li>
      <li>Math Assessments with Quorvane Career</li>
      <li class="cont">Database (powered by the Quorvane®</li>
      <li class="cont">Framework for Mathematics)</li>
    </ul>
  </section>

  <div class="icon orange" style="left:46px;top:526px" role="img" aria-label="Icon of a handshake"></div>
  <section class="block left on-dark" style="left:47px;top:545px;width:560px">
    <h2 style="position:absolute;left:138px;top:0">CAREER<br>ENGAGED</h2>
    <p style="margin-top:109px">Students are motivated and inspired to develop<br>career skills and seek employment opportunities<br>that meet both personal and community needs.</p>
    <ul>
      <li>Career Awareness &amp; Exposure</li>
      <li>Purposeful Learning Connected to Careers</li>
    </ul>
  </section>

  <div class="icon dark" style="left:1053px;top:526px" role="img" aria-label="Icon of a person with a briefcase climbing steps"></div>
  <section class="block right" style="right:48px;top:550px;width:560px">
    <h2 style="margin-right:115px">CAREER<br>WISE</h2>
    <p style="margin-top:20px">Students have insight into personal values and<br>interests, as well as the economic realities of the job<br>market, that supports informed career decisions.</p>
    <ul>
      <li>Career Pathways</li>
      <li>Career Exploration</li>
      <li>Educator Career Guides</li>
    </ul>
  </section>

  <section class="hub">
    <h3>Data-Informed and<br>Evidence-Based Practices</h3>
    <p>BrightlaneWork relies on robust labor<br>market data tools and sound educational<br>research to guide our development efforts<br>and encourage the use of informed career<br>readiness practices in educational settings.</p>
    <h4>BLW Data Tools</h4>
    <ul>
      <li>Labor Market Data System</li>
      <li>Employer Surveys</li>
      <li>Regional Labor Market Reports</li>
    </ul>
  </section>
</main>
</body>
</html>
```